We would like to create a flyer with our logo I have attached and would like you to add the QuillmoreBID logo at the bottom.
I would like the flyer to have a urban vintage style to it.
Please add:
Email: Info@quillmorebid-example.co.uk
Twitter account: @Quillmorebid
Facebook account: Larkmoor Row Retro & Curio Fair
Address: Larkmoor Row, Fennick Vale, ZN4 7QP
Dates: Saturday 27 september 2014
Saturday 25 October 2014
Saturday 29 November 2014.
Please hight light the dates and the location.

Every one.

• Market Deco

• My project should be eye catching.
• Dates and location should be clear.
• Please use this font: ‘Market Deco’
• Please source images which will suit the logo and style of layout.
• Colours which will contrast with the logo.
• Colour of logo is: purple is P95 -16c
• The layout on the word doc I like.

```html
<!DOCTYPE html>
<html lang="en">
<head>
<meta charset="utf-8">
<title>Larkmoor Row Retro &amp; Curio Fair</title>
<link href="https://fonts.googleapis.com/css2?family=Josefin+Sans:wght@400;600;700&display=swap" rel="stylesheet">
<style>
  :root {
    --page: #e9e6e1;
    --teal-deep: #0b3f4a;
    --teal: #1b7f86;
    --aqua: #3fb3c9;
    --sky: #7fd2ec;
    --ink: #1d1410;
    --white: #ffffff;
    --plum: #2e1f4e;
    --logo-purple: #7b3a73;
    --panel: rgba(235, 240, 242, 0.82);
  }
  * { margin: 0; padding: 0; box-sizing: border-box; }
  html, body { width: 998px; height: 1200px; overflow: hidden; background: var(--page); }
  body { font-family: "Josefin Sans", sans-serif; }

  .flyer {
    position: absolute; left: 36px; top: 0; width: 926px; height: 1200px; overflow: hidden;
    background: linear-gradient(160deg, var(--teal-deep) 0%, var(--teal) 35%, var(--aqua) 60%, #2a8d8c 85%, #1e6a5e 100%);
  }
  .street-scene {
    position: absolute; left: 0; top: 420px; width: 926px; height: 620px;
    background:
      radial-gradient(ellipse at 40% 50%, rgba(127, 210, 236, 0.75), rgba(63, 179, 201, 0.25) 60%, transparent 80%),
      linear-gradient(180deg, transparent, rgba(30, 110, 150, 0.35));
  }
  .title {
    position: absolute; left: 0; width: 100%; top: 46px; text-align: center;
    color: var(--white); font-weight: 700; font-size: 66px; line-height: 106px; letter-spacing: 3px;
    text-transform: uppercase; text-shadow: 3px 4px 0 rgba(0, 0, 0, 0.55);
  }
  .welcome-ribbon {
    position: absolute; left: 200px; top: 255px; width: 526px; height: 178px;
    background: radial-gradient(ellipse at center, rgba(140, 190, 160, 0.55), rgba(60, 130, 110, 0.2) 70%, transparent);
    border-radius: 40px;
  }
  .welcome {
    position: absolute; left: 0; width: 100%; top: 340px; text-align: center;
    color: var(--ink); font-weight: 700; font-size: 50px; letter-spacing: 6px; opacity: 0.85;
  }
  .market-sign {
    position: absolute; left: 169px; top: 470px; width: 631px; height: 53px;
    background: var(--plum); border: 2px solid #c9c3d8; outline: 2px solid var(--plum);
    color: var(--white); font-weight: 600; font-size: 30px; line-height: 55px; text-align: center; letter-spacing: 1px;
    text-transform: uppercase;
  }
  .heading {
    position: absolute; left: 0; width: 100%; text-align: center;
    color: var(--ink); font-weight: 700; font-size: 68px; letter-spacing: 2px; text-transform: uppercase;
  }
  .heading.address { top: 555px; }
  .heading.dates { top: 703px; }
  .rule { position: absolute; top: 575px; }
  .address-line {
    position: absolute; left: 0; width: 100%; top: 630px; text-align: center;
    color: var(--ink); font-weight: 600; font-size: 30px; letter-spacing: 1px; text-transform: uppercase;
  }
  .date-list { position: absolute; left: 0; width: 100%; top: 785px; list-style: none; }
  .date-list li {
    height: 52px; text-align: center; color: var(--ink); font-weight: 600; font-size: 33px;
    letter-spacing: 1px; text-transform: uppercase;
  }
  .day {
    display: inline-block; width: 38px; height: 38px; border-radius: 50%;
    background: var(--ink); color: var(--white); font-size: 26px; line-height: 42px; margin: 0 4px; vertical-align: 2px;
  }
  .contact-panel {
    position: absolute; left: 74px; top: 949px; width: 538px; height: 132px;
    background: var(--panel); border-radius: 14px; padding: 12px 0 0 32px;
  }
  .contact-row { display: flex; align-items: center; height: 38px; color: var(--plum); font-size: 16px; font-weight: 600; text-transform: uppercase; }
  .contact-row .mark {
    width: 32px; height: 32px; border-radius: 50%; background: var(--plum); margin-right: 18px;
    display: flex; align-items: center; justify-content: center; flex: none;
  }
  .logo-panel {
    position: absolute; left: 625px; top: 949px; width: 231px; height: 132px;
    background: var(--panel); border-radius: 14px; display: flex; align-items: center; justify-content: center; gap: 10px;
  }
  .logo-dot { width: 16px; height: 16px; background: var(--logo-purple); }
  .logo-name { color: var(--logo-purple); font-weight: 700; font-size: 24px; }
  .website {
    position: absolute; left: 0; width: 100%; top: 1118px; text-align: center;
    color: var(--white); font-weight: 600; font-size: 29px; letter-spacing: 1px; text-transform: uppercase;
  }
</style>
</head>
<body>
  <main class="flyer">
    <div class="street-scene" role="img" aria-label="Blue-washed photo of a high street with shopfronts and scrolling flourishes"></div>

    <h1 class="title">Larkmoor Row Retro<br>&amp; Curio Fair</h1>

    <div class="welcome-ribbon" role="img" aria-label="Vintage ribbon banner ornament with stars"></div>
    <p class="welcome">WELCOME</p>

    <div class="market-sign">Larkmoor Row Retro &amp; Curio Fair</div>

    <svg class="rule" style="left:200px" width="120" height="20" viewBox="0 0 120 20"><path d="M2 10 Q30 2 60 10 T118 10" fill="none" stroke="#fff" stroke-width="3"/></svg>
    <svg class="rule" style="left:606px" width="120" height="20" viewBox="0 0 120 20"><path d="M2 10 Q30 18 60 10 T118 10" fill="none" stroke="#fff" stroke-width="3"/></svg>

    <h2 class="heading address">Address</h2>
    <p class="address-line">Larkmoor Row, Fennick Vale, ZN4 7QP</p>

    <h2 class="heading dates">Dates</h2>
    <ul class="date-list">
      <li>Saturday <span class="day">27</span> September 2014</li>
      <li>Saturday <span class="day">25</span> October 2014</li>
      <li>Saturday <span class="day">29</span> November 2014</li>
    </ul>

    <section class="contact-panel">
      <div class="contact-row">
        <span class="mark"><svg width="18" height="13" viewBox="0 0 18 13"><rect x="1" y="1" width="16" height="11" fill="none" stroke="#fff" stroke-width="1.6"/><path d="M1 1 L9 7 L17 1" fill="none" stroke="#fff" stroke-width="1.6"/></svg></span>
        Info@quillmorebid-example.co.uk
      </div>
      <div class="contact-row"><span class="mark"></span>@Quillmorebid</div>
      <div class="contact-row"><span class="mark"></span>Larkmoor Row Retro &amp; Curio Fair</div>
    </section>

    <section class="logo-panel">
      <span class="logo-dot"></span>
      <span class="logo-name">QuillmoreBID</span>
    </section>

    <p class="website">www.quillmorebid-example.co.uk</p>
  </main>
</body>
</html>
```